Northfield Builders Guild Business card

We are looking for a new business card design with photo included.
Our business is a nonprofit construction contractor membership organization. We offer business education, assist with business setup and licensing, provide safety training, and provide a member directory.
URL: www.builderslinkguild.org
Color code:
CMYK: 0 cyan, 42 magenta, 100 yellow, 0 black for Print.
Hexidecimal: #FF9900
RGB: R 255; G 153; B 0

```html
<!DOCTYPE html>
<html lang="en">
<head>
<meta charset="utf-8">
<title>Northfield Builders Guild — Business Card</title>
<link rel="stylesheet" href="https://fonts.googleapis.com/css2?family=Oswald:wght@500&family=Open+Sans:wght@400;800&family=Montserrat:wght@400&display=swap">
<style>
  :root {
    --page: #e9e6e1;
    --card: #ffffff;
    --orange: #f7981d;
    --ink: #333333;
    --ink-soft: #3d3d3d;
    --rule: #555555;
  }
  html, body {
    margin: 0;
    width: 1200px;
    height: 969px;
    overflow: hidden;
    background: var(--page);
  }
  .card {
    position: absolute;
    left: 100px;
    top: 200px;
    width: 1000px;
    height: 569px;
    background: var(--card);
    border-radius: 30px;
    overflow: hidden;
    box-shadow: 0 6px 18px rgba(0,0,0,0.18);
  }
  .name-band {
    position: absolute;
    left: 0;
    top: 96px;
    width: 100%;
    height: 148px;
    background: var(--orange);
  }
  .person {
    position: absolute;
    left: 560px;
    top: 124px;
  }
  .person-name {
    margin: 0;
    font-family: "Oswald", sans-serif;
    font-weight: 500;
    font-size: 48px;
    line-height: 1;
    color: var(--ink);
    transform: scaleX(0.82);
    transform-origin: left;
    letter-spacing: 0.5px;
  }
  .person-title {
    margin: 8px 0 0;
    font-family: "Open Sans", sans-serif;
    font-size: 17px;
    color: var(--ink-soft);
  }
  .org-name {
    position: absolute;
    left: 103px;
    top: 352px;
    width: 330px;
    margin: 0;
    font-family: "Open Sans", sans-serif;
    font-weight: 800;
    font-size: 36px;
    line-height: 1.05;
    color: var(--ink);
    text-transform: uppercase;
    letter-spacing: -0.5px;
  }
  .divider {
    position: absolute;
    left: 520px;
    top: 315px;
    width: 1px;
    height: 195px;
    background: var(--rule);
  }
  .address {
    position: absolute;
    left: 560px;
    top: 282px;
    margin: 0;
    font-family: "Open Sans", sans-serif;
    font-style: normal;
    font-size: 18px;
    line-height: 25px;
    color: var(--ink);
  }
  .contact-list {
    position: absolute;
    left: 557px;
    top: 349px;
    margin: 0;
    padding: 0;
    list-style: none;
  }
  .contact-item {
    display: flex;
    align-items: center;
    height: 34px;
    margin-bottom: 8.5px;
    font-family: "Montserrat", sans-serif;
    font-size: 14px;
    letter-spacing: 2.6px;
    color: var(--ink);
  }
  .contact-icon {
    width: 34px;
    height: 34px;
    flex: none;
  }
  .contact-item .value { margin-left: 28px; }
  .contact-item.wide .value { margin-left: 16px; letter-spacing: 2.2px; }
</style>
</head>
<body>
  <main class="card">
    <div class="name-band"></div>
    <div class="person">
      <h1 class="person-name">DANIEL REYES</h1>
      <p class="person-title">CEO/Managing Director</p>
    </div>

    <p class="org-name">Northfield<br>Builders Guild</p>

    <div class="divider"></div>

    <address class="address">118 Harlow Street NE<br>Suite 210, Northfield MN 55057</address>

    <ul class="contact-list">
      <li class="contact-item">
        <svg class="contact-icon" viewBox="0 0 34 34" aria-hidden="true">
          <circle cx="17" cy="17" r="17" fill="var(--orange)"/>
          <path d="M12 9c1 0 2 2.5 2.6 3.6.4.8-.6 1.6-1.2 2.2.8 2 2.3 3.6 4.4 4.6.6-.6 1.4-1.6 2.2-1.2 1.1.6 3.5 1.7 3.5 2.6 0 1.5-1.6 3-3.2 3-5.6-.3-11.3-6-11.4-11.6C8.9 10.6 10.5 9 12 9z" fill="#fff"/>
        </svg>
        <span class="value">507-555-0143</span>
      </li>
      <li class="contact-item">
        <svg class="contact-icon" viewBox="0 0 34 34" aria-hidden="true">
          <circle cx="17" cy="17" r="17" fill="var(--orange)"/>
          <path d="M17 7 6.5 16.5h3V26h5.5v-6h4v6h5.5v-9.5h3z" fill="#fff"/>
        </svg>
        <span class="value">507-555-0188</span>
      </li>
      <li class="contact-item wide">
        <svg class="contact-icon" viewBox="0 0 34 34" aria-hidden="true">
          <circle cx="17" cy="17" r="17" fill="var(--orange)"/>
          <rect x="8" y="11" width="18" height="12.5" rx="1" fill="none" stroke="#fff" stroke-width="1.8"/>
          <path d="M8.5 11.5 17 18.5l8.5-7" fill="none" stroke="#fff" stroke-width="1.8"/>
        </svg>
        <span class="value">dreyes@buildersguildmail.org</span>
      </li>
      <li class="contact-item wide">
        <svg class="contact-icon" viewBox="0 0 34 34" aria-hidden="true">
          <circle cx="17" cy="17" r="17" fill="var(--orange)"/>
          <g fill="none" stroke="#fff" stroke-width="1.5">
            <circle cx="17" cy="17" r="9"/>
            <ellipse cx="17" cy="17" rx="4" ry="9"/>
            <path d="M8 17h18M9.5 12.5h15M9.5 21.5h15"/>
          </g>
        </svg>
        <span class="value">www.builderslinkguild.org</span>
      </li>
    </ul>
  </main>
</body>
</html>
```